WP website design Pellow - Brantz (Contest)

We need a wordpress design that will incorporate a professional color scheme with company logo in a clean layout. The design needs to consider that this will be developed on a responsive theme. Colors are red and black of the logo and and an accent color. Client wants a 'modern' look.

Industry/Entity Type

It Company

Font styles to use
Serif
Sans Serif

Colors

Designer to choose colors to be used in the design.

Requirements
Must have
• Must Have:
- Navigation: 1) Home; 2) Auctions; 3) Real Estate Listings 4) Assets For Sale 5) Services 6) About Us 7) Contact Us

Site will have slideshow - image is attached. Colors will be those in the logo, red and black with maybe an accent color. A site the client mentions liking is Mubrelbids.com for the use of color and layout.

Widgets: Featured Auctions, 2) Email signup form; 3) Testimonials blog widget; 5) Featured Video; Footer will have affiliation logo and contact info.

Home page content:
We are a family owned and operated business with over 25 years of real estate experience in Clinton and surrounding areas in Western Oklahoma. We know that purchasing a home is one of the most important decisions a person can make, and we strive to make it a successful and enjoyable experience for you!
Enjoy our website and please call if you have any questions or would like to make an appointment to view property!
Also, take a moment to look at our Auction Calendar for upcoming auction dates. Auctions are a great opportunity for great deals and rare finds, not to mention A LOT OF FUN!!

Widgets: 1) Featured Properties; 2) Call to action for Sellers 3) Testimonials blog/widget
Nice to have
• use of dropdown menus

```html
<!DOCTYPE html>
<html lang="en">
<head>
<meta charset="utf-8">
<title>Pellow Auction &amp; Real Estate</title>
<link href="https://fonts.googleapis.com/css2?family=Source+Sans+3:wght@400;600;700&display=swap" rel="stylesheet">
<style>
:root{
  --red:#c40d10;
  --ink:#222;
  --text:#444;
  --line:#ddd;
  --btn:#e9e9e9;
}
*{box-sizing:border-box;margin:0;padding:0}
html,body{width:786px;height:1200px;overflow:hidden;background:#fff}
body{position:relative;font-family:"Source Sans 3",Arial,sans-serif;color:var(--text)}
.abs{position:absolute}
.hero{left:0;top:0;width:786px;height:402px;background:linear-gradient(180deg,#c9d6df 0%,#9fae7e 25%,#5d6f35 50%,#8a8a55 75%,#b8a575 100%)}
.header-band{left:0;top:0;width:786px;height:58px;background:linear-gradient(180deg,#eef2f5,#dfe6ea)}
.brand{left:82px;top:10px;font-weight:700;font-size:26px;line-height:30px;color:var(--red);letter-spacing:.5px;display:flex;align-items:center;gap:6px}
.brand i{width:10px;height:10px;background:var(--red);display:inline-block}
.brand-sub{left:106px;top:40px;font-size:8px;line-height:10px;color:var(--ink)}
.btn-top{top:19px;height:19px;font-size:10px;color:#fff;display:flex;align-items:center;justify-content:center;border-radius:2px}
.signin{left:585px;width:45px;background:var(--red)}
.register{left:638px;width:57px;background:#333}
.nav{left:65px;top:58px;width:656px;height:28px;background:var(--red);display:flex;align-items:center;padding-left:23px;gap:21px}
.nav a{color:#fff;text-decoration:none;font-size:11.5px}
.intro{left:81px;top:141px;width:270px;height:133px;background:rgba(20,20,20,.82);border-radius:3px;padding:18px 18px}
.intro h1{font-weight:400;font-size:19px;color:#fff;margin-bottom:7px}
.intro p{font-size:7.6px;line-height:1.35;color:#eee;margin-bottom:10px}
.btn-red{display:inline-block;background:var(--red);color:#fff;font-size:10px;padding:3px 9px}
.dots{left:655px;top:243px;display:flex;gap:7px}
.dots span{width:12px;height:12px;border-radius:50%;background:#111}
.dots span:first-child{background:#eee}
.alert{left:65px;top:344px;width:656px;height:58px;background:rgba(25,25,25,.85);display:flex;align-items:center}
.alert h3{color:#fff;font-size:13px;font-weight:700;margin-left:35px}
.alert p{color:#fff;font-size:7.8px;line-height:1.3;margin-left:16px;width:180px}
.alert .email{width:188px;height:26px;background:#fff;border-radius:2px;margin-left:15px;font-size:8px;color:#999;padding:8px}
.alert .subscribe{width:104px;height:26px;background:#3a3a3a;color:#fff;font-size:11px;margin-left:15px;display:flex;align-items:center;justify-content:center}
.section-title{font-size:17px;color:var(--ink);font-weight:400}
.auction{left:101px;width:390px;height:150px}
.auction .thumb{position:absolute;left:0;top:0;width:126px;height:114px}
.auction .info{position:absolute;left:141px;top:-1px;width:250px}
.auction h2{font-weight:400;font-size:18px;color:var(--red);margin-bottom:3px}
.auction .lead{font-size:10px;color:var(--text);margin-bottom:6px}
.auction .meta{font-size:8px;line-height:1.5;color:var(--text)}
.auction .tools{display:flex;gap:17px;margin-top:9px}
.auction .tools svg{width:13px;height:13px}
.details{display:inline-block;background:var(--btn);font-size:8px;padding:2px 11px;margin-top:3px;color:var(--ink)}
.pager{left:171px;top:936px;display:flex;gap:6px}
.pager span{height:19px;min-width:20px;padding:0 6px;border:1px solid #ccc;font-size:9px;display:flex;align-items:center;justify-content:center;color:#333;font-weight:600}
.pager .wide{width:39px}
.divider{left:490px;top:415px;width:1px;height:545px;background:var(--line)}
.side-title{font-size:16.5px;color:var(--ink);font-weight:400}
.arrows{left:671px;top:424px;display:flex;gap:2px}
.arrows span{width:8px;height:8px;border-radius:50%;background:#333}
.avatar{left:505px;top:460px;width:50px;height:50px;border-radius:50%;background:linear-gradient(#cab7a6,#8a6e5c);border:2px solid #ddd}
.avatar-name{left:524px;top:512px;font-size:7.5px;color:var(--ink)}
.red-sub{font-size:12px;color:var(--red)}
.body-small{font-size:7.8px;line-height:1.3;color:var(--text);text-align:justify}
.blog-thumb{left:503px;width:66px;height:66px}
.blog-bar{left:503px;width:66px;height:12px;background:#f1f1f1;border:1px solid #ddd}
.blog-head{left:577px;font-size:11.5px;color:var(--ink);display:flex;align-items:center;gap:5px}
.blog-head i{width:6px;height:6px;border-radius:50%;background:var(--red)}
.blog-head i.off{background:#ddd}
.video{left:509px;top:805px;width:204px;height:149px;background:linear-gradient(180deg,#d6c9b0,#8d8777 55%,#5a5a55)}
.play{left:590px;top:857px;width:40px;height:40px;border-radius:50%;background:rgba(40,40,40,.7)}
.affiliate{left:171px;top:1001px;font-size:12px;color:var(--ink)}
.badge{top:996px;height:26px;background:#ccc}
.foot-nav{left:146px;top:1055px;display:flex;gap:21px;font-size:11px;color:#666}
.foot-info{left:0;width:786px;text-align:center;font-size:9.5px;color:var(--ink)}
.foot-mail{color:var(--red)}
.social{left:334px;top:1142px;display:flex;gap:4px}
.social span{width:27px;height:27px;background:var(--red)}
.copy{left:0;top:1178px;width:786px;text-align:center;font-size:7.5px;color:#aaa}
.bottom-line{left:0;top:1193px;width:786px;height:7px;background:#111}
</style>
</head>
<body>
<div class="abs hero" role="img" aria-label="Slideshow photo of an auction sign beside a fence in a field"></div>
<div class="abs header-band"></div>
<div class="abs brand"><i></i>PELLOW</div>
<div class="abs brand-sub">Auction &amp; Real Estate</div>
<div class="abs btn-top signin">Signin</div>
<div class="abs btn-top register">Register</div>
<nav class="abs nav">
  <a>Home</a><a>Auctions</a><a>Real Estate Listings</a><a>Assets For Sale</a><a>Services</a><a>About Us</a><a>Contact Us</a>
</nav>
<div class="abs intro">
  <h1>Pellow Auctions &amp; Real Estate</h1>
  <p>Lorem ipsum dolor sit amet, consectetur adipisicing elit, sed do eiusmod tempor incididunt ut labore et dolore magna aliqua. Ut enim ad minim veniam.</p>
  <span class="btn-red">Register Now</span>
</div>
<div class="abs dots"><span></span><span></span><span></span></div>
<div class="abs alert">
  <h3>Auction Alerts!</h3>
  <p>Sign Up to Receive Exclusive Email Updates on Upcoming Pellow Auction Events!</p>
  <div class="email">Email</div>
  <div class="subscribe">Subscribe</div>
</div>

<h2 class="abs section-title" style="left:101px;top:422px">Featured Auctions</h2>

<div class="abs auction" style="top:465px">
  <div class="thumb" role="img" aria-label="City skyline at sunset" style="background:linear-gradient(180deg,#e8b77c,#a98466 55%,#555)"></div>
  <div class="info">
    <h2>Test Auction</h2>
    <p class="lead">Just testing and adding an auction for the fun of it</p>
    <p class="meta">LIVE ON-SITE AUCTION Location:<br>48 Elm Court, Fairview, KY 40100<br>Begins: 12/19/14 at 7:00 PM EST<br>Ends: 12/20/14 at 7:00 PM EST</p>
    <div class="tools">
      <svg viewBox="0 0 14 14"><circle cx="6" cy="6" r="4" fill="none" stroke="#555" stroke-width="1.5"/><path d="M9 9l4 4" stroke="#555" stroke-width="1.5"/></svg>
      <svg viewBox="0 0 14 14"><rect x="1" y="2" width="12" height="11" fill="#d98b2b"/><rect x="1" y="2" width="12" height="3" fill="#444"/></svg>
      <svg viewBox="0 0 14 14"><rect x="1" y="4" width="9" height="7" fill="#777"/><path d="M10 6l3-2v7l-3-2z" fill="#777"/></svg>
      <svg viewBox="0 0 14 14"><circle cx="7" cy="7" r="4" fill="none" stroke="#2a5fa8" stroke-width="2" stroke-dasharray="2 1.5"/></svg>
      <svg viewBox="0 0 14 14"><path d="M3 3v5a4 4 0 008 0V3" fill="none" stroke="#444" stroke-width="2"/></svg>
    </div>
    <span class="details">Details</span>
  </div>
</div>

<div class="abs auction" style="top:623px">
  <div class="thumb" role="img" aria-label="Modern house with pool at dusk" style="background:linear-gradient(180deg,#9fb4c7,#8c8f88 55%,#5fb6c4)"></div>
  <div class="info">
    <h2>Test Auction</h2>
    <p class="lead">Just testing and adding an auction for the fun of it</p>
    <p class="meta">LIVE ON-SITE AUCTION Location:<br>48 Elm Court, Fairview, KY 40100<br>Begins: 12/19/14 at 7:00 PM EST<br>Ends: 12/20/14 at 7:00 PM EST</p>
    <div class="tools">
      <svg viewBox="0 0 14 14"><circle cx="6" cy="6" r="4" fill="none" stroke="#555" stroke-width="1.5"/><path d="M9 9l4 4" stroke="#555" stroke-width="1.5"/></svg>
      <svg viewBox="0 0 14 14"><rect x="1" y="2" width="12" height="11" fill="#d98b2b"/><rect x="1" y="2" width="12" height="3" fill="#444"/></svg>
      <svg viewBox="0 0 14 14"><rect x="1" y="4" width="9" height="7" fill="#777"/><path d="M10 6l3-2v7l-3-2z" fill="#777"/></svg>
      <svg viewBox="0 0 14 14"><circle cx="7" cy="7" r="4" fill="none" stroke="#2a5fa8" stroke-width="2" stroke-dasharray="2 1.5"/></svg>
      <svg viewBox="0 0 14 14"><path d="M3 3v5a4 4 0 008 0V3" fill="none" stroke="#444" stroke-width="2"/></svg>
    </div>
    <span class="details">Details</span>
  </div>
</div>

<div class="abs auction" style="top:774px">
  <div class="thumb" role="img" aria-label="Construction workers at a building site" style="background:linear-gradient(180deg,#3f78c6,#7d8fa3 55%,#b9c23c)"></div>
  <div class="info">
    <h2>Test Auction</h2>
    <p class="lead">Just testing and adding an auction for the fun of it</p>
    <p class="meta">LIVE ON-SITE AUCTION Location:<br>48 Elm Court, Fairview, KY 40100<br>Begins: 12/19/14 at 7:00 PM EST<br>Ends: 12/20/14 at 7:00 PM EST</p>
    <div class="tools">
      <svg viewBox="0 0 14 14"><circle cx="6" cy="6" r="4" fill="none" stroke="#555" stroke-width="1.5"/><path d="M9 9l4 4" stroke="#555" stroke-width="1.5"/></svg>
      <svg viewBox="0 0 14 14"><rect x="1" y="2" width="12" height="11" fill="#d98b2b"/><rect x="1" y="2" width="12" height="3" fill="#444"/></svg>
      <svg viewBox="0 0 14 14"><rect x="1" y="4" width="9" height="7" fill="#777"/><path d="M10 6l3-2v7l-3-2z" fill="#777"/></svg>
      <svg viewBox="0 0 14 14"><circle cx="7" cy="7" r="4" fill="none" stroke="#2a5fa8" stroke-width="2" stroke-dasharray="2 1.5"/></svg>
      <svg viewBox="0 0 14 14"><path d="M3 3v5a4 4 0 008 0V3" fill="none" stroke="#444" stroke-width="2"/></svg>
    </div>
    <span class="details">Details</span>
  </div>
</div>

<div class="abs pager">
  <span class="wide">Prev</span><span>1</span><span>2</span><span>3</span><span>4</span><span>5</span><span>6</span><span>...</span><span>22</span><span class="wide">Next</span>
</div>

<div class="abs divider"></div>

<h2 class="abs side-title" style="left:505px;top:416px">Testimonials</h2>
<div class="abs arrows"><span></span><span></span></div>
<div class="abs avatar" role="img" aria-label="Portrait of the client giving the testimonial"></div>
<div class="abs avatar-name">Maren</div>
<div class="abs red-sub" style="left:566px;top:450px">Auctions Specials</div>
<p class="abs body-small" style="left:566px;top:467px;width:126px">Aliquam quaerat voluptatem. Ut enim ad minima veniam, quis nostrum exercitationem ullam corporis suscipit laboriosam, nisi ut aliquid ex ea commodi consequatu</p>

<h2 class="abs side-title" style="left:502px;top:547px">Blog Listings</h2>
<div class="abs blog-thumb" role="img" aria-label="Large stone house at night" style="top:578px;background:linear-gradient(180deg,#1f3f8a,#6c5a45 60%,#3e3a2e)"></div>
<div class="abs blog-bar" style="top:644px"></div>
<div class="abs blog-head" style="top:576px"><i></i>Auctions Listing</div>
<p class="abs body-small" style="left:580px;top:600px;width:124px">Aliquam quaerat voluptatem. Ut enim ad minima veniam, quis nostrum exercitationem ullam corporis suscipit laboriosam, nisi ut aliquid ex ea commodi consequatu</p>
<div class="abs blog-thumb" role="img" aria-label="Family house with green lawn" style="top:676px;background:linear-gradient(180deg,#a8c2dc,#b8a98d 55%,#5f8a3a)"></div>
<div class="abs blog-bar" style="top:742px"></div>
<div class="abs blog-head" style="top:675px"><i class="off"></i>Auctions Listing</div>
<p class="abs body-small" style="left:580px;top:699px;width:124px">Aliquam quaerat voluptatem. Ut enim ad minima veniam, quis nostrum exercitationem ullam corporis suscipit laboriosam, nisi ut aliquid ex ea commodi consequatu</p>

<h2 class="abs side-title" style="left:505px;top:771px">Featured Video</h2>
<div class="abs video" role="img" aria-label="Video still of a city skyline from above"></div>
<div class="abs play"></div>
<svg class="abs" style="left:605px;top:868px" width="12" height="18" viewBox="0 0 12 18"><path d="M1 1l10 8-10 8z" fill="#fff"/></svg>

<div class="abs affiliate">Affiliate</div>
<div class="abs badge" style="left:238px;width:46px"></div>
<div class="abs badge" style="left:295px;width:25px"></div>
<div class="abs badge" style="left:327px;width:28px;border-radius:50%"></div>
<div class="abs badge" style="left:362px;width:26px;border-radius:50%"></div>
<div class="abs badge" style="left:396px;width:47px"></div>
<div class="abs badge" style="left:461px;width:48px"></div>
<div class="abs badge" style="left:522px;width:94px"></div>

<div class="abs foot-nav"><span>Home</span><span>Auctions</span><span>Real Estate Listings</span><span>Assets For Sale</span><span>Services</span><span>About Us</span><span>Contact Us</span></div>
<div class="abs foot-info" style="top:1080px">Pellow Auction &amp; Real Estate, LLC &nbsp;|&nbsp; 1450 W. Garnet Ave - Ashford Vale, Arkansas</div>
<div class="abs foot-info" style="top:1096px">Phone &nbsp;555-014-2290 &nbsp;&nbsp;Fax &nbsp;555-014-2291</div>
<div class="abs foot-info foot-mail" style="top:1112px">info@pellowauction.com</div>
<div class="abs social"><span></span><span></span><span></span><span></span></div>
<div class="abs copy">© 2014.www.companyname.com</div>
<div class="abs bottom-line"></div>
</body>
</html>
```